Industry / Entity Type

Financial consultancy / advisers

Current site is: http://www.brightmoor-counsel.com

Looking for a complete overhaul of this site, we are after a clean modern look. Will require the ability to easily add, update and remove content, hence the WordPress design.
Example:
Add case studies
Industry documentation (downloadable brochures / flyers and such)

What we like from our current site is the colour the fonts and the logo (the city of London) we would like to have other city outlines (NYC and Tokyo, Hong Kong, Singapore).

The site will be used by our potential clients to get in contact and re-view the case studies, if possible would like to have a client login area where they can download our documents like NDA’s etc and T&C’s.

Task Outline

Create a Web Design (Coded - Design and coding required)
Designer must provide full implementation/coding depending on the platform chosen by the client (i.e. WordPress theme, HTML/CSS, bootstrap etc.)

Task Description

I need a full website built that must work on desktop and mobile. I can provide the London city skyline and the font file, which we have used. Some stock industrial photos will be required.

Requirements:

*Splash page
*What We Do
*How We do it
*Who Are We? To have the same information and links as the current site
*Why use us?
*Clients: To have the same information and links as the current site
*Partners: To have the same information and links as the current site
*Contact:

Target Market(s)

Financial institutions trading Equities, Futures, Options, Forex and Fixed Income.
Regulators, Exchanges, ECN’s
Buy side firms and Sell side firms

Industry/Entity Type

Financial

Coding

Coded - Design and coding required

Number of Pages Required

5+ page

Font styles to use
Sans Serif

Colors
f04a50

Requirements
Must have
• Splash page
• What We Do
• How We do it
• Who Are We? To have the same information and links as the current site
• Why use us?
• Clients: To have the same information and links as the current site
• Partners: To have the same information and links as the current site
• Contact:

```html
<!DOCTYPE html>
<html lang="en">
<head>
<meta charset="utf-8">
<title>Brightmoor Counsel Advisers</title>
<link href="https://fonts.googleapis.com/css2?family=Open+Sans:ital,wght@0,400;0,600;1,400&family=Questrial&family=Syncopate:wght@400;700&display=swap" rel="stylesheet">
<style>
:root{
  --brand:#f04a50;
  --brand-dark:#d93c42;
  --ink:#2b2b2b;
  --text:#666;
  --muted:#8a8a8a;
  --line:#e4e4e4;
  --soft:#f6f6f6;
  --white:#fff;
}
*{box-sizing:border-box;margin:0;padding:0}
html,body{width:1200px;height:3141px;overflow:hidden}
body{position:relative;background:var(--white);font-family:"Open Sans",Arial,sans-serif;color:var(--text)}
.abs{position:absolute}
.center-x{transform:translateX(-50%)}
.heading{font-family:"Questrial",Arial,sans-serif;color:var(--ink);font-size:27px;letter-spacing:1px;text-align:center;text-transform:uppercase;font-weight:400}
.heading-rule{position:absolute;left:50%;transform:translateX(-50%);width:130px;height:1px;background:#ccc}
.heading-rule::after{content:"";position:absolute;left:40px;width:50px;height:2px;top:-.5px;background:var(--brand)}
.intro{font-size:12.5px;line-height:21px;text-align:center;color:var(--muted);width:640px;left:280px}
.btn{display:inline-block;background:var(--brand);color:var(--white);font-size:12px;text-transform:uppercase;border-radius:22px;text-align:center;letter-spacing:.5px}

/* header */
.site-header{top:0;left:0;width:1200px;height:159px}
.brand-mark{left:130px;top:62px;width:26px;height:26px;border:2px solid var(--ink)}
.brand-name{left:168px;top:52px;font-family:"Syncopate",Arial,sans-serif;font-size:16px;font-weight:700;color:var(--ink);letter-spacing:1px;line-height:23px;white-space:nowrap}
.contact-chip{top:58px;display:flex;align-items:center;gap:12px}
.chip-icon{width:40px;height:40px;border:1px solid var(--line);border-radius:50%;display:flex;align-items:center;justify-content:center}
.chip-label{font-size:11px;color:var(--muted);line-height:16px}
.chip-value{font-size:13px;color:var(--brand);line-height:18px;text-transform:uppercase;white-space:nowrap}
.chip-value.phone{font-size:15px}

/* nav */
.main-nav{top:159px;left:0;width:1200px;height:55px;border-top:1px solid var(--line);border-bottom:1px solid var(--line)}
.nav-item{top:19px;font-size:11.5px;color:#333;text-transform:uppercase;letter-spacing:.4px;white-space:nowrap}
.nav-item.active{color:var(--brand)}
.nav-active-bar{top:-1px;left:130px;width:96px;height:3px;background:var(--brand)}

/* hero */
.hero{top:214px;left:0;width:1200px;height:502px;background:radial-gradient(ellipse at 65% 40%,#2f7f93 0%,#17485a 35%,#0b1c28 75%)}
.hero-photo{inset:0}
.hero-caption{left:595px;top:196px;width:473px}
.hero-title{background:rgba(10,20,28,.85);color:var(--white);font-family:"Syncopate",Arial,sans-serif;font-size:22px;letter-spacing:3px;padding:10px 18px;text-transform:uppercase;text-align:center}
.hero-text{margin-left:26px;background:rgba(10,20,28,.7);color:#d6dde2;font-size:11px;line-height:19px;padding:8px 16px;text-transform:uppercase}
.hero-dot{top:444px;width:20px;height:20px;border-radius:50%;background:#e8e8e8;display:flex;align-items:center;justify-content:center}

/* welcome */
.welcome-text{left:132px;top:905px;width:520px;font-size:12.5px;line-height:22px;color:var(--text)}
.welcome-text p{margin-bottom:16px}
.device{border-radius:6px}

/* what we do */
.services{top:1265px;left:0;width:1200px;height:517px;background:var(--soft);border-top:1px solid #eee;border-bottom:1px solid #eee}
.service-card{top:152px;width:214px;height:294px;background:var(--white);border:1px solid #e6e6e6;text-align:center}
.service-icon{margin:26px auto 0;width:92px;height:92px;border:1px solid #ddd;border-radius:50%;display:flex;align-items:center;justify-content:center}
.service-title{margin-top:18px;font-size:12.5px;font-weight:600;color:var(--ink);text-transform:uppercase;letter-spacing:.3px}
.service-text{margin:8px auto 0;width:160px;font-size:11px;line-height:18px;color:var(--muted)}
.service-card .btn{margin-top:14px;width:98px;height:32px;line-height:32px;font-size:10px}
.slider-arrow{width:34px;height:34px;border-radius:50%;background:#d8d8d8;display:flex;align-items:center;justify-content:center}

/* case studies */
.case-list{left:657px;top:1994px;list-style:none}
.case-list li{display:flex;align-items:center;gap:20px;height:42px;font-size:12px;color:#555}
.case-bullet{width:30px;height:30px;border:1px solid #e2e2e2;border-radius:50%;display:flex;align-items:center;justify-content:center}

/* team */
.team{top:2297px;left:0;width:1200px;height:388px;background:var(--brand)}
.team .heading{color:var(--white)}
.team-rule{position:absolute;left:50%;transform:translateX(-50%);width:130px;height:1px;background:rgba(255,255,255,.8)}
.member{top:138px;width:220px;text-align:center;color:var(--white)}
.member-photo{margin:0 auto;width:96px;height:96px;border-radius:50%;border:4px solid rgba(255,255,255,.55);background:linear-gradient(160deg,#c9c2bb,#7d7670)}
.member-name{margin-top:24px;font-size:12.5px;text-transform:uppercase;letter-spacing:.4px}
.member-role{font-size:11.5px;line-height:20px}
.member-link{font-size:10.5px;font-style:italic;font-weight:600;text-decoration:underline}

/* clients */
.clients{top:2685px;left:0;width:1200px;height:117px;border-bottom:1px solid var(--line)}
.client{top:44px;display:flex;align-items:center;gap:8px;font-family:"Open Sans",Arial,sans-serif;font-weight:600;font-size:19px;color:#3a3a3a;white-space:nowrap}
.client-sq{width:14px;height:14px;background:#3a3a3a}

/* footer */
.footer-col{top:2846px}
.footer-heading{font-size:13px;font-weight:600;color:#333;text-transform:uppercase;letter-spacing:.4px;margin-bottom:18px}
.footer-text{font-size:11.5px;line-height:21px;color:var(--muted)}
.footer-line{display:flex;gap:10px}
.read-more{font-size:11.5px;color:var(--brand)}
.newsletter-input{width:222px;height:36px;border:1px solid #ccc;border-radius:18px;padding-left:18px;font-size:10px;line-height:34px;color:#aaa;text-transform:uppercase}
.newsletter .btn{margin-top:8px;width:110px;height:34px;line-height:34px;font-size:11px}
.social{display:flex;gap:5px;margin-top:22px}
.social span{width:24px;height:24px;border-radius:50%}
.copyright{top:3078px;left:0;width:1200px;height:63px;border-top:1px solid var(--line);font-size:11.5px;color:var(--muted);text-align:center;line-height:60px}
</style>
</head>
<body>

<header class="site-header abs">
  <div class="brand-mark abs"></div>
  <div class="brand-name abs">BRIGHTMOOR<br>COUNSEL</div>

  <div class="contact-chip abs" style="left:593px">
    <div class="chip-icon"><svg width="16" height="12" viewBox="0 0 16 12"><rect x="0.5" y="0.5" width="15" height="11" fill="var(--brand)"/><path d="M1 1 L8 7 L15 1" stroke="#fff" fill="none"/></svg></div>
    <div><div class="chip-label">Email :</div><div class="chip-value">info@brightmoor-counsel.com</div></div>
  </div>
  <div class="contact-chip abs" style="left:870px">
    <div class="chip-icon"><svg width="16" height="16" viewBox="0 0 16 16"><path d="M3 1 L6 4 L4.5 6 C5.5 8.5 7.5 10.5 10 11.5 L12 10 L15 13 L13 15 C7 14 2 9 1 3 Z" fill="var(--brand)"/></svg></div>
    <div><div class="chip-label">Phone :</div><div class="chip-value phone">+44(0)20 7946 0321</div></div>
  </div>
</header>

<nav class="main-nav abs">
  <div class="nav-active-bar abs"></div>
  <span class="nav-item active abs center-x" style="left:178px">Home</span>
  <span class="nav-item abs center-x" style="left:291px">What we do</span>
  <span class="nav-item abs center-x" style="left:425px">How we do it</span>
  <span class="nav-item abs center-x" style="left:561px">Who are we</span>
  <span class="nav-item abs center-x" style="left:697px">Why use us</span>
  <span class="nav-item abs center-x" style="left:810px">Clients</span>
  <span class="nav-item abs center-x" style="left:923px">Partners</span>
  <span class="nav-item abs center-x" style="left:1039px">Contact</span>
</nav>

<section class="hero abs">
  <div class="hero-photo abs" role="img" aria-label="Businessman in a suit holding a tablet with glowing financial charts and data graphics"></div>
  <div class="hero-caption abs">
    <div class="hero-title">Financial Technology</div>
    <div class="hero-text">Duis aute irure dolor in reprehenderit in voluptate velit esse cillum dolore eu fugiat nulla pariatur occaecat cupidatat...</div>
  </div>
  <div class="hero-dot abs" style="left:1022px"><svg width="8" height="8" viewBox="0 0 8 8"><path d="M5.5 1 L2.5 4 L5.5 7" stroke="#333" stroke-width="1.6" fill="none"/></svg></div>
  <div class="hero-dot abs" style="left:1048px"><svg width="8" height="8" viewBox="0 0 8 8"><path d="M2.5 1 L5.5 4 L2.5 7" stroke="#333" stroke-width="1.6" fill="none"/></svg></div>
</section>

<section class="welcome">
  <h1 class="heading abs" style="left:0;width:1200px;top:768px">Welcome to Brightmoor Counsel</h1>
  <div class="heading-rule" style="top:808px"></div>
  <p class="intro abs" style="top:824px">Sint occaecat cupidatat non proident, sunt in culpa qui officia deserunt mollit anim id est laborum Nemo enim ipsam voluptatem quia voluptas sit aspernatur aut odit aut fugit...</p>
  <div class="welcome-text abs">
    <p>Since founding Brightmoor Counsel Advisers in 2014 we have dedicated ourselves to the provision of services. What differentiates us from other advisers or consultancies is a genuine motivation to see our clients succeed. Today's technology allows...</p>
    <p>Our clients to take their knowledge to the market in ways that previous generations could only dream of. That's why BCA is dedicated to seeing you choose the right technology strategy, ensuring you maintain a competitive edge over your peers...</p>
  </div>
  <span class="btn abs" style="left:132px;top:1089px;width:162px;height:42px;line-height:42px">Learn more info</span>
  <div class="device abs" role="img" aria-label="Desktop monitor showing a world map with financial charts on screen" style="left:743px;top:863px;width:325px;height:293px;background:linear-gradient(160deg,#e9eef2 0%,#2d7fa0 30%,#0f3650 70%,#cfd4d8 100%)"></div>
</section>

<section class="services abs">
  <h2 class="heading abs" style="left:0;width:1200px;top:62px">What we do it</h2>
  <div class="heading-rule" style="top:104px"></div>

  <div class="slider-arrow abs" style="left:79px;top:276px"><svg width="10" height="10" viewBox="0 0 10 10"><path d="M6.5 1.5 L3 5 L6.5 8.5" stroke="#fff" stroke-width="1.8" fill="none"/></svg></div>
  <div class="slider-arrow abs" style="left:1084px;top:276px"><svg width="10" height="10" viewBox="0 0 10 10"><path d="M3.5 1.5 L7 5 L3.5 8.5" stroke="#fff" stroke-width="1.8" fill="none"/></svg></div>

  <article class="service-card abs" style="left:132px">
    <div class="service-icon"><svg width="48" height="44" viewBox="0 0 48 44"><circle cx="17" cy="24" r="11" fill="none" stroke="var(--brand)" stroke-width="7" stroke-dasharray="5 3.6"/><circle cx="17" cy="24" r="4" fill="var(--brand)"/><circle cx="36" cy="12" r="7" fill="none" stroke="var(--brand)" stroke-width="5" stroke-dasharray="3.5 2.6"/><circle cx="36" cy="12" r="2.5" fill="var(--brand)"/></svg></div>
    <h3 class="service-title">Process Outsourcing</h3>
    <p class="service-text">Proin gravida nibh vel velit auctor aliquet. Aenean sollicitudin, lor bendum auctor...</p>
    <span class="btn">Learn more</span>
  </article>
  <article class="service-card abs" style="left:373px">
    <div class="service-icon"><svg width="46" height="46" viewBox="0 0 46 46"><circle cx="26" cy="19" r="15" fill="none" stroke="var(--brand)" stroke-width="4"/><path d="M15 30 L4 41" stroke="var(--brand)" stroke-width="6" stroke-linecap="round"/><ellipse cx="26" cy="19" rx="8" ry="5" fill="none" stroke="var(--brand)" stroke-width="2"/><circle cx="26" cy="19" r="2.5" fill="var(--brand)"/></svg></div>
    <h3 class="service-title">Research</h3>
    <p class="service-text">Proin gravida nibh vel velit auctor aliquet. Aenean sollicitudin, lor bendum auctor...</p>
    <span class="btn">Learn more</span>
  </article>
  <article class="service-card abs" style="left:614px">
    <div class="service-icon"><svg width="48" height="40" viewBox="0 0 48 40"><path d="M24 4 L46 14 L24 24 L2 14 Z" fill="var(--brand)"/><path d="M12 19 V30 C16 35 32 35 36 30 V19 L24 25 Z" fill="var(--brand)"/><path d="M42 16 V28" stroke="var(--brand)" stroke-width="2"/></svg></div>
    <h3 class="service-title">Training</h3>
    <p class="service-text">Proin gravida nibh vel velit auctor aliquet. Aenean sollicitudin, lor bendum auctor...</p>
    <span class="btn">Learn more</span>
  </article>
  <article class="service-card abs" style="left:854px">
    <div class="service-icon"><svg width="46" height="48" viewBox="0 0 46 48"><path d="M23 10 C14 10 10 17 12 24 C13 28 17 30 17 35 H29 C29 30 33 28 34 24 C36 17 32 10 23 10 Z" fill="none" stroke="var(--brand)" stroke-width="3"/><rect x="17" y="37" width="12" height="3" fill="var(--brand)"/><rect x="19" y="42" width="8" height="3" fill="var(--brand)"/><path d="M23 2 V6 M8 8 L11 11 M38 8 L35 11 M2 22 H6 M40 22 H44" stroke="var(--brand)" stroke-width="2.5"/><path d="M23 20 V30" stroke="var(--brand)" stroke-width="2.5"/></svg></div>
    <h3 class="service-title">Advice</h3>
    <p class="service-text">Proin gravida nibh vel velit auctor aliquet. Aenean sollicitudin, lor bendum auctor...</p>
    <span class="btn">Learn more</span>
  </article>
</section>

<section class="case-studies">
  <h2 class="heading abs" style="left:0;width:1200px;top:1836px">Case studies</h2>
  <div class="heading-rule" style="top:1878px"></div>
  <p class="intro abs" style="top:1893px">Sint occaecat cupidatat non proident, sunt in culpa qui officia deserunt mollit anim id est laborum Nemo enim ipsam voluptatem quia voluptas sit aspernatur aut odit aut fugit...</p>
  <div class="device abs" role="img" aria-label="Desktop monitor showing hands on a laptop over a blue world map" style="left:260px;top:1979px;width:305px;height:220px;background:linear-gradient(160deg,#3b3b3b 0%,#6c6257 35%,#2f86b8 60%,#cfd3d6 100%)"></div>
  <ul class="case-list abs">
    <li><span class="case-bullet"><svg width="12" height="12" viewBox="0 0 12 12"><path d="M1 5 H3.5 V11 H1 Z M4.5 5 L7 1 C8 1 8.5 2 8 3.5 L7.5 5 H10.5 C11.3 5 11.6 5.8 11.3 6.5 L9.8 10.5 C9.6 11 9.2 11 8.8 11 H4.5 Z" fill="var(--brand)"/></svg></span>Infrastructure Case Study</li>
    <li><span class="case-bullet"><svg width="12" height="12" viewBox="0 0 12 12"><path d="M1 5 H3.5 V11 H1 Z M4.5 5 L7 1 C8 1 8.5 2 8 3.5 L7.5 5 H10.5 C11.3 5 11.6 5.8 11.3 6.5 L9.8 10.5 C9.6 11 9.2 11 8.8 11 H4.5 Z" fill="var(--brand)"/></svg></span>Tech-Startup-Case</li>
    <li><span class="case-bullet"><svg width="12" height="12" viewBox="0 0 12 12"><path d="M1 5 H3.5 V11 H1 Z M4.5 5 L7 1 C8 1 8.5 2 8 3.5 L7.5 5 H10.5 C11.3 5 11.6 5.8 11.3 6.5 L9.8 10.5 C9.6 11 9.2 11 8.8 11 H4.5 Z" fill="var(--brand)"/></svg></span>Tech-Due Diligence</li>
    <li><span class="case-bullet"><svg width="12" height="12" viewBox="0 0 12 12"><path d="M1 5 H3.5 V11 H1 Z M4.5 5 L7 1 C8 1 8.5 2 8 3.5 L7.5 5 H10.5 C11.3 5 11.6 5.8 11.3 6.5 L9.8 10.5 C9.6 11 9.2 11 8.8 11 H4.5 Z" fill="var(--brand)"/></svg></span>Training : Capital Markets Training</li>
    <li><span class="case-bullet"><svg width="12" height="12" viewBox="0 0 12 12"><path d="M1 5 H3.5 V11 H1 Z M4.5 5 L7 1 C8 1 8.5 2 8 3.5 L7.5 5 H10.5 C11.3 5 11.6 5.8 11.3 6.5 L9.8 10.5 C9.6 11 9.2 11 8.8 11 H4.5 Z" fill="var(--brand)"/></svg></span>Product development &amp; Technology Strategy</li>
  </ul>
</section>

<section class="team abs">
  <h2 class="heading abs" style="left:0;width:1200px;top:48px">Our team</h2>
  <div class="team-rule" style="top:88px"></div>
  <div class="member abs" style="left:135px">
    <div class="member-photo" role="img" aria-label="Portrait photo of Owen Harcastle"></div>
    <div class="member-name">Owen Harcastle</div><div class="member-role">Director</div><div class="member-link">Click View More Information</div>
  </div>
  <div class="member abs" style="left:372px">
    <div class="member-photo" role="img" aria-label="Portrait photo of Simon Pellow"></div>
    <div class="member-name">Simon Pellow</div><div class="member-role">Director</div><div class="member-link">Click View More Information</div>
  </div>
  <div class="member abs" style="left:610px">
    <div class="member-photo" role="img" aria-label="Portrait photo of Gareth Linwood"></div>
    <div class="member-name">Gareth Linwood</div><div class="member-role">New Business Director</div><div class="member-link">Click View More Information</div>
  </div>
  <div class="member abs" style="left:847px">
    <div class="member-photo" role="img" aria-label="Portrait photo of Helena Brookes" style="background:linear-gradient(160deg,#bdbdbd,#6a6a6a)"></div>
    <div class="member-name">Helena Brookes</div><div class="member-role">Non-Executive Director</div><div class="member-link">Click View More Information</div>
  </div>
</section>

<section class="clients abs">
  <svg class="abs" style="left:90px;top:50px" width="10" height="14" viewBox="0 0 10 14"><path d="M8 1 L2 7 L8 13" stroke="#555" stroke-width="1.6" fill="none"/></svg>
  <div class="client abs center-x" style="left:195px"><span class="client-sq"></span>Norvale</div>
  <div class="client abs center-x" style="left:386px">Keystone Partners</div>
  <div class="client abs center-x" style="left:582px">Arcline Data</div>
  <div class="client abs center-x" style="left:760px">Tradewell</div>
  <div class="client abs center-x" style="left:998px">Harbourmark</div>
  <svg class="abs" style="left:1104px;top:50px" width="10" height="14" viewBox="0 0 10 14"><path d="M2 1 L8 7 L2 13" stroke="#555" stroke-width="1.6" fill="none"/></svg>
</section>

<footer>
  <div class="footer-col abs" style="left:132px;width:200px">
    <h4 class="footer-heading">About BCA</h4>
    <p class="footer-text">Since founding Brightmoor Counsel Advisers in 2014 we have dedicated ourselves to the provision...</p>
    <p class="read-more" style="margin-top:6px">Read More +</p>
  </div>
  <div class="footer-col abs" style="left:406px;width:420px">
    <h4 class="footer-heading">Contact Details</h4>
    <div style="display:flex;gap:40px">
      <div class="footer-line">
        <svg width="10" height="14" viewBox="0 0 10 14" style="margin-top:4px;flex:none"><path d="M5 0 C2 0 0 2.2 0 5 C0 8.5 5 14 5 14 C5 14 10 8.5 10 5 C10 2.2 8 0 5 0 Z" fill="var(--brand)"/><circle cx="5" cy="5" r="1.8" fill="#fff"/></svg>
        <p class="footer-text">Suite 4 Alder Court,<br>Elmfield,<br>Northbridge,<br>Herts,<br>NB12 4QT<br>Company No:07381265<br>VAT No: 4815926</p>
      </div>
      <div>
        <div class="footer-line"><svg width="11" height="11" viewBox="0 0 16 16" style="margin-top:5px;flex:none"><path d="M3 1 L6 4 L4.5 6 C5.5 8.5 7.5 10.5 10 11.5 L12 10 L15 13 L13 15 C7 14 2 9 1 3 Z" fill="var(--brand)"/></svg><p class="footer-text">Phone : +44(0)20 7946 0321</p></div>
        <div class="footer-line" style="margin-top:16px"><svg width="12" height="9" viewBox="0 0 16 12" style="margin-top:6px;flex:none"><rect width="16" height="12" fill="var(--brand)"/><path d="M1 1 L8 7 L15 1" stroke="#fff" fill="none"/></svg><p class="footer-text">Email : info@brightmoor counsel</p></div>
      </div>
    </div>
  </div>
  <div class="footer-col newsletter abs" style="left:846px;width:240px">
    <h4 class="footer-heading">Newsletter</h4>
    <div class="newsletter-input">Email Address</div>
    <span class="btn">Subscribe</span>
    <div class="social">
      <span style="background:#3b5a9a"></span>
      <span style="background:#1a7bb9"></span>
      <span style="background:#f0a030"></span>
      <span style="background:#3fb3e8"></span>
      <span style="background:#d23b30"></span>
    </div>
  </div>
  <div class="copyright abs">Copyrights © brightmoor counsel .2017 | Allrights Reserved.</div>
</footer>

</body>
</html>
```